Web site for small printshop

I am looking for a website for small printshop in Iceland, mainly serving university students and artist.

We print posters, flyers, business cards and more.

In addition to our current website, I would like to include design tool, (fx. www.quarvelpad.example, www.trindomap.example or something similar) jobs upload, shopping chart.
Updates

Great work, I am really amazed of the quality of work i am seeing here.

Really way beyond my expectation

GOOD JOB - all of you ! 

Hi all.

The designs submitted have been great, way better than expected.
I really did not expect this level of quality.

Some have been asking me for feedback on their designs, and I will try 
to send some feedback here, without spoiling your creativity.

Likes:
- when the colors of my logo is used in menus, buttons etc.
- simple, not to crowded look.

Dislikes.
- Dark and heavy design
- Lot of text and buttons (crowded look)

Extra info.
- top line (before menus) will contain: Tel - email - language
- menu line will have 5 categories: Home - service - submission of works - FAQ - about us
- 3 large buttons:  Job submit - Job design - ask for offer

LOVE YOUR WORK - great designs so far :)

Target Market(s)

University Students, Artists. Age group 20-30

Industry/Entity Type

University

Requirements
Must have
• The website must be easy to use, clean looking.

```html
<!DOCTYPE html>
<html lang="en">
<head>
<meta charset="utf-8">
<title>Prentvik – Contact Us</title>
<link href="https://fonts.googleapis.com/css2?family=Oswald:wght@300&family=Source+Sans+3:wght@400;600&display=swap" rel="stylesheet">
<style>
:root{
  --red:#e8412f;
  --green:#17a34a;
  --ink:#2a2a2a;
  --muted:#6b6b6b;
  --topbar:#f5f5f5;
  --band:#e2e2e2;
  --form-bg:#f7f7f7;
  --field-border:#dcdcdc;
  --footer:#3a393a;
  --footer-base:#141414;
  --footer-text:#d6d6d6;
  --social:#bdbdbd;
}
*{box-sizing:border-box;margin:0;padding:0}
html,body{width:1200px;height:1032px;overflow:hidden;background:#fff}
body{position:relative;font-family:"Source Sans 3",sans-serif;color:var(--ink)}
.abs{position:absolute}

.top-bar{left:0;top:0;width:1200px;height:29px;background:var(--topbar)}
.top-bar .info{right:172px;top:6px;font-size:11.5px;font-weight:600;display:flex;gap:8px;align-items:center;position:absolute}
.top-bar .sep{width:2px;height:13px;background:var(--ink)}
.call{color:var(--red)}
.mail{color:var(--green)}
.lang{color:var(--muted)}

.brand{left:171px;top:43px;display:flex;align-items:center;gap:9px}
.brand-mark{width:32px;height:32px;background:var(--red)}
.brand-name{font-size:27px;font-weight:600;color:var(--ink);letter-spacing:.3px}

.main-nav{top:53px;left:562px;font-size:16.5px;font-weight:600;color:#444}
.main-nav span{position:absolute;white-space:nowrap}

.hero-line{left:173px;top:137px;font-family:"Oswald",sans-serif;font-weight:300;font-size:26px;line-height:30px;color:#555;width:320px}
.hero-photo{left:629px;top:93px;width:326px;height:165px;background:linear-gradient(160deg,#c9a88a,#8c6a55 50%,#5e6c8e)}

.section-band{left:0;top:258px;width:1200px;height:44px;background:var(--band)}
.section-band h1{position:absolute;left:178px;top:9px;font-size:20.5px;font-weight:400}

.contact-text{left:178px;top:362px;font-size:15.5px;line-height:19px;width:220px}
.contact-phone{left:178px;top:436px;font-size:15.5px;line-height:19px;color:#555}
.contact-phone .num{color:var(--red)}
.contact-mail{left:178px;top:479px;font-size:15.5px;color:var(--green)}
.social{left:177px;top:518px;display:flex;gap:6px}
.social span{width:24px;height:24px;border-radius:50%;background:var(--social)}

.map-frame{left:626px;top:331px;width:386px;height:266px;background:#e6e6e6;padding:6px}
.map-fill{width:100%;height:100%;background:linear-gradient(135deg,#ece8df,#f1eee7 55%,#e4e0d6)}

.form-area{left:0;top:618px;width:1200px;height:281px;background:var(--form-bg)}
.form-area h2{position:absolute;left:171px;top:13px;font-size:19.5px;font-weight:400}
.field{position:absolute;background:#fff;border:1px solid var(--field-border);font-size:12.5px;color:#888;padding:9px 9px}
.submit{position:absolute;left:936px;top:212px;width:92px;height:31px;background:var(--red);color:#fff;font-weight:600;font-size:15px;display:flex;align-items:center;justify-content:center}

.site-footer{left:0;top:899px;width:1200px;height:75px;background:var(--footer)}
.footer-brand{position:absolute;left:171px;top:22px;display:flex;align-items:center;gap:8px}
.footer-brand .brand-mark{width:28px;height:28px;background:#8a8a8a}
.footer-brand .brand-name{font-size:23px;color:#8a8a8a}
.footer-nav span{position:absolute;top:28px;font-size:12.5px;color:var(--footer-text);white-space:nowrap}

.footer-base{left:0;top:974px;width:1200px;height:58px;background:var(--footer-base)}
.footer-base p{position:absolute;left:171px;top:26px;font-size:10.5px;color:#9a9a9a;font-family:Arial,sans-serif}
</style>
</head>
<body>
<header class="abs top-bar">
  <div class="info">
    <span class="call">CALL US : 09 555 0142</span><span class="sep"></span>
    <span class="mail">Mailto : hello@prentvik.example</span><span class="sep"></span>
    <span class="lang">Language: English</span>
  </div>
</header>

<div class="abs brand"><span class="brand-mark"></span><span class="brand-name">PRENTVIK</span></div>

<nav class="abs main-nav">
  <span style="left:0">Home</span>
  <span style="left:91px">Services</span>
  <span style="left:184px">Submit Works</span>
  <span style="left:330px">FAQ</span>
  <span style="left:400px">About us</span>
</nav>

<p class="abs hero-line">Want to reduce your print costs and Productivity ?</p>
<div class="abs hero-photo" role="img" aria-label="Photo of a smiling group of young students"></div>

<div class="abs section-band"><h1>Contact Us</h1></div>

<p class="abs contact-text">Praesent pellentesque diam vitae nibh aliquam faucibus. Vestibulum</p>
<p class="abs contact-phone">Phone : <span class="num">+1 (555) 014 - 2290</span><br><span class="num" style="margin-left:57px">+1 (555) 014 - 2290</span></p>
<p class="abs contact-mail">Mailto : hello@prentvik.example</p>
<div class="abs social" aria-label="Social links"><span></span><span></span><span></span><span></span></div>

<div class="abs map-frame"><div class="map-fill" role="img" aria-label="Street map showing the shop location"></div></div>

<section class="abs form-area">
  <h2>Send Us Mail</h2>
  <div class="field" style="left:171px;top:53px;width:409px;height:35px">Name</div>
  <div class="field" style="left:171px;top:104px;width:409px;height:35px">Email</div>
  <div class="field" style="left:171px;top:163px;width:408px;height:35px">Mobile Number</div>
  <div class="field" style="left:620px;top:53px;width:408px;height:144px">Message</div>
  <div class="submit">SUBMIT</div>
</section>

<footer class="abs site-footer">
  <div class="footer-brand"><span class="brand-mark"></span><span class="brand-name">PRENTVIK</span></div>
  <div class="footer-nav">
    <span style="left:579px">Home</span>
    <span style="left:641px">Quote Request</span>
    <span style="left:764px">About us</span>
    <span style="left:830px">Supplying your artwork</span>
    <span style="left:980px">Contact Us</span>
  </div>
</footer>
<div class="abs footer-base"><p>Copyright @ 2012 www.pagewright.example &nbsp;Privacy Policy | Disclaimer | Resources</p></div>
</body>
</html>
```